Homemaking training schools needs a Business Card design

Designer, Hello!

No special requirements, good-looking enough.
--------------------------------------------------------------------------

Name: Marcus Dole
Chairman
Tel: 0574-71948263
Mobile: 13857420916
Email: kelvora@mailnest.example
Web: www.prt2019.example
Add: No.258, LanpingJie, BeiyuanQu, Ningbo, Zhejiang

LOGO
Ningbo PRT Homemaking Training School

Target Market(s)

pregnant women, mothers, infants, the elderly and families, including cleaning, cooking, nursing training.

Industry/Entity Type

Business

Contact Information for Business Card

Name: Marcus Dole
Chairman
Tel: 0574-71948263
Mobile: 13857420916
Email: kelvora@mailnest.example
Web: www.prt2019.example

LOGO

Font styles to use
Serif
Sans Serif
Decorative

Requirements
Nice to have
• Feels: clean, specifications, safety, comfort, warmth and happiness.

```html
<!DOCTYPE html>
<html lang="en">
<head>
<meta charset="utf-8">
<title>PeiRenTang Business Card</title>
<link rel="stylesheet" href="https://fonts.googleapis.com/css2?family=Open+Sans:ital,wght@0,400;0,600;1,400&display=swap">
<style>
  :root {
    --stage: #4d4d4d;
    --paper: #ffffff;
    --ink-dark: #000000;
    --brand-blue: #1f74bb;
    --brand-pink: #e3168c;
    --text-grey: #555555;
    --white: #ffffff;
  }
  * { margin: 0; padding: 0; box-sizing: border-box; }
  html, body {
    width: 1105px;
    height: 1200px;
    overflow: hidden;
    background: var(--stage);
    font-family: "Open Sans", Arial, sans-serif;
  }
  .card {
    position: absolute;
    left: 196px;
    width: 720px;
    height: 412px;
  }
  .card--front { top: 146px; background: var(--paper); }
  .card--back { top: 602px; background: var(--ink-dark); }

  /* brand placeholder: plain name with one circle beside it */
  .brand {
    position: absolute;
    display: flex;
    align-items: center;
  }
  .brand__dot {
    flex: none;
    border-radius: 50%;
    background: var(--brand-pink);
  }
  .brand__name {
    font-family: "Open Sans", Arial, sans-serif;
    font-weight: 600;
    color: var(--brand-blue);
    line-height: 1;
    white-space: nowrap;
  }

  .card--front .brand { right: 46px; top: 96px; gap: 12px; }
  .card--front .brand__dot { width: 18px; height: 18px; }
  .card--front .brand__name { font-size: 40px; }

  .card--back .brand { left: 0; width: 100%; justify-content: center; top: 162px; gap: 16px; }
  .card--back .brand__dot { width: 24px; height: 24px; }
  .card--back .brand__name { font-size: 54px; }

  /* front: person */
  .person {
    position: absolute;
    left: 32px;
    top: 242px;
    width: 656px;
  }
  .person__name {
    font-size: 25px;
    font-weight: 600;
    color: var(--brand-blue);
    line-height: 1.2;
  }
  .person__role {
    display: flex;
    align-items: flex-end;
    font-size: 19px;
    color: var(--brand-pink);
    line-height: 1.2;
  }
  .person__role::after {
    content: "";
    flex: 1;
    height: 1.5px;
    background: var(--brand-pink);
    margin-left: 2px;
    margin-bottom: 3px;
  }

  /* front: contacts */
  .contacts {
    position: absolute;
    left: 32px;
    top: 316px;
    width: 656px;
    display: flex;
    justify-content: space-between;
    font-size: 16px;
    color: var(--text-grey);
    line-height: 27px;
  }
  .contacts__address { font-style: normal; }
  .contacts__item {
    display: flex;
    align-items: center;
    gap: 8px;
    white-space: nowrap;
  }
  .contacts__icon {
    width: 16px;
    height: 16px;
    fill: var(--brand-blue);
    flex: none;
  }

  /* back: web */
  .web {
    position: absolute;
    left: 0;
    width: 100%;
    top: 333px;
    text-align: center;
    font-style: italic;
    font-size: 18px;
    letter-spacing: 5px;
    color: var(--white);
  }
</style>
</head>
<body>

<section class="card card--front">
  <div class="brand">
    <span class="brand__dot"></span>
    <span class="brand__name">PeiRenTang</span>
  </div>

  <div class="person">
    <p class="person__name">Marcus Dole</p>
    <p class="person__role">Chairman</p>
  </div>

  <div class="contacts">
    <address class="contacts__address">
      <p>No.258, LanpingJie</p>
      <p>BeiyuanQu, Ningbo, Zhejiang</p>
    </address>
    <div class="contacts__col">
      <p class="contacts__item">
        <svg class="contacts__icon" viewBox="0 0 24 24" aria-hidden="true"><path d="M6.6 10.8c1.4 2.8 3.8 5.1 6.6 6.6l2.2-2.2c.3-.3.7-.4 1-.2 1.1.4 2.3.6 3.6.6.6 0 1 .4 1 1V20c0 .6-.4 1-1 1C10.6 21 3 13.4 3 4c0-.6.4-1 1-1h3.5c.6 0 1 .4 1 1 0 1.3.2 2.5.6 3.6.1.3 0 .7-.2 1z"/></svg>
        0574-71948263
      </p>
      <p class="contacts__item">
        <svg class="contacts__icon" viewBox="0 0 24 24" aria-hidden="true"><path d="M7 1h10a2 2 0 0 1 2 2v18a2 2 0 0 1-2 2H7a2 2 0 0 1-2-2V3a2 2 0 0 1 2-2zm0 4v13h10V5zm5 14.5a1 1 0 1 0 0 2 1 1 0 0 0 0-2z"/></svg>
        13857420916
      </p>
    </div>
    <div class="contacts__col">
      <p class="contacts__item">
        <svg class="contacts__icon" viewBox="0 0 24 24" aria-hidden="true"><path d="M2 5h20v14H2zm2 2v.5l8 5 8-5V7zm0 2.8V17h16V9.8l-8 5z"/></svg>
        kelvora@mailnest.example
      </p>
      <p class="contacts__item">
        <svg class="contacts__icon" viewBox="0 0 24 24" aria-hidden="true"><path d="M12 2a10 10 0 1 0 0 20 10 10 0 0 0 0-20zm-1 17.9A8 8 0 0 1 4.2 10.8L9 15.6v1a2 2 0 0 0 2 2zm6.9-2.5A2 2 0 0 0 16 16h-1v-3a1 1 0 0 0-1-1H8v-2h2a1 1 0 0 0 1-1V7h2a2 2 0 0 0 2-2v-.4a8 8 0 0 1 2.9 12.8z"/></svg>
        www.prt2019.example
      </p>
    </div>
  </div>
</section>

<section class="card card--back">
  <div class="brand">
    <span class="brand__dot"></span>
    <span class="brand__name">PeiRenTang</span>
  </div>
  <p class="web">www.prt2019.example</p>
</section>

</body>
</html>
```